Animal Eye Clinic needs a Business card

We are a new veterinary ophthalmology practice (Ridgeline Pet Vision Care) and we need a business card designed. We only see animal eyes - we are not a regular veterinary clinic. We already have a logo. We are looking for a professional, good looking business card to hand out to our clients. We are looking for something simple but professional and contemporary. Our logo is likely the only picture/graphic that needs to be on the card.
Updates

Contact Information for Business Card

Delia Vossman, BSc, DVM, MSc, DipACVO
Veterinary Ophthalmologist

Phone: 250.418.3927
Email: ridgelinepetvisioncare@mailbox-example.net
Website: ridgelinepetvisioncare-example.net
Address: 1874 Thornbury Rd
Kelowna, BC, V1X 4M9

Colors

Designer to choose colors to be used in the design.

Requirements
Must have
• Our logo (attached)

```html
<!DOCTYPE html>
<html lang="en">
<head>
<meta charset="utf-8">
<title>Ridgeline Pet Vision Care – Business Card</title>
<link rel="stylesheet" href="https://fonts.googleapis.com/css2?family=Source+Sans+3:wght@400;700&display=swap">
<style>
  :root {
    --teal: #0a97a8;
    --white: #ffffff;
    --ink: #6d6e70;
    --backdrop: #e6e7e8;
    --card-w: 474px;
    --card-h: 269px;
  }
  * { box-sizing: border-box; margin: 0; padding: 0; }
  html, body {
    width: 1200px;
    height: 1200px;
    overflow: hidden;
  }
  body {
    position: relative;
    background: var(--backdrop);
    font-family: "Source Sans 3", "Myriad Pro", Arial, sans-serif;
  }
  .card {
    position: absolute;
    left: 363px;
    width: var(--card-w);
    height: var(--card-h);
    display: flex;
    align-items: center;
    padding-left: 24px;
  }
  .card--front { top: 151px; background: var(--white); color: var(--ink); }
  .card--back  { top: 746px; background: var(--teal); color: var(--white); }

  .brand {
    display: flex;
    align-items: center;
    gap: 10px;
    width: 196px;
  }
  .brand__dot {
    width: 34px;
    height: 34px;
    border-radius: 50%;
    flex: none;
  }
  .brand__name {
    font-weight: 700;
    font-size: 17px;
    line-height: 1.05;
    text-transform: uppercase;
    letter-spacing: 0.3px;
  }
  .card--front .brand__dot { background: var(--teal); }
  .card--front .brand__name { color: var(--teal); }
  .card--back .brand__dot { background: var(--white); }
  .card--back .brand__name { color: var(--white); }

  .divider {
    width: 1px;
    align-self: center;
    margin: 0 8px 0 6px;
    flex: none;
  }
  .card--front .divider { height: 30px; background: var(--ink); }
  .card--back .divider { height: 58px; background: var(--white); }

  .practitioner {
    font-size: 10.5px;
    line-height: 1.45;
  }
  .contact-list {
    list-style: none;
    font-size: 9.8px;
    line-height: 1.55;
  }
  .contact-list li {
    display: flex;
    align-items: center;
    gap: 6px;
  }
  .contact-list svg {
    width: 9px;
    height: 9px;
    flex: none;
    fill: var(--white);
  }
</style>
</head>
<body>

<section class="card card--front" aria-label="Business card front">
  <div class="brand">
    <span class="brand__dot"></span>
    <span class="brand__name">Ridgeline Pet<br>Vision Care</span>
  </div>
  <span class="divider"></span>
  <div class="practitioner">
    <p class="practitioner__name">Delia Vossman, BSc, DVM, MSc, DipACVO</p>
    <p class="practitioner__title">Veterinary Ophthalmologist</p>
  </div>
</section>

<section class="card card--back" aria-label="Business card back">
  <div class="brand">
    <span class="brand__dot"></span>
    <span class="brand__name">Ridgeline Pet<br>Vision Care</span>
  </div>
  <span class="divider"></span>
  <ul class="contact-list">
    <li>
      <svg viewBox="0 0 10 10" aria-hidden="true"><path d="M2 0.5 L3.6 0.5 L4.2 3 L3 3.8 Q4 6.2 6.2 7 L7 5.8 L9.5 6.4 L9.5 8 Q9.5 9.5 8 9.5 Q0.5 9 0.5 2 Q0.5 0.5 2 0.5 Z"/></svg>
      <span>250.418.3927</span>
    </li>
    <li>
      <svg viewBox="0 0 10 10" aria-hidden="true"><path d="M0.5 2 H9.5 V8.5 H0.5 Z M0.5 2 L5 5.5 L9.5 2" stroke="#0a97a8" stroke-width="0.8"/></svg>
      <span>ridgelinepetvisioncare@mailbox-example.net</span>
    </li>
    <li>
      <svg viewBox="0 0 10 10" aria-hidden="true"><circle cx="5" cy="5" r="4.5"/><path d="M0.5 5 H9.5 M5 0.5 V9.5 M5 0.5 Q2 5 5 9.5 M5 0.5 Q8 5 5 9.5" stroke="#0a97a8" stroke-width="0.7" fill="none"/></svg>
      <span>ridgelinepetvisioncare-example.net</span>
    </li>
    <li>
      <svg viewBox="0 0 10 10" aria-hidden="true"><circle cx="5" cy="5" r="4.5"/><path d="M5 2.2 Q6.8 2.2 6.8 4 Q6.8 5.4 5 7.8 Q3.2 5.4 3.2 4 Q3.2 2.2 5 2.2 Z" fill="#0a97a8"/></svg>
      <span>1874 Thornbury Rd Kelowna, BC, V1X 4M9</span>
    </li>
  </ul>
</section>

</body>
</html>
```